Kestrel Facilities Business Card Design

We would now like to design business cards with the new Kestrel Facilities logo

Target Market(s)

Professional

Industry/Entity Type

Professional services

Contact Information for Business Card

Employee name, title, phone number, email address, corporate office address and logo.

Font styles to use
Sans Serif

Colors
0054AA
0677BA
7BADD7
CADEEF
E8F1F8

Requirements
Must have
• My logo
Should not have
• any other pictures or images besides my logo

```html
<!DOCTYPE html>
<html lang="en">
<head>
<meta charset="UTF-8">
<title>Kestrel Facilities Business Card</title>
<link href="https://fonts.googleapis.com/css2?family=Oswald:wght@500&family=Arimo:wght@400&display=swap" rel="stylesheet">
<style>
  :root {
    --brand-blue: #0b80e6;
    --swoosh-grey: #707070;
    --card-white: #ffffff;
    --ink: #1c1c1c;
    --backdrop: #e9ecef;
  }
  * { margin: 0; padding: 0; box-sizing: border-box; }
  html, body { width: 1200px; height: 900px; overflow: hidden; }
  body {
    background: var(--backdrop);
    display: flex;
    flex-direction: column;
    align-items: center;
    justify-content: center;
    gap: 44px;
    font-family: "Arimo", Arial, sans-serif;
  }
  .card {
    position: relative;
    width: 630px;
    height: 360px;
    overflow: hidden;
    box-shadow: 0 6px 18px rgba(0,0,0,0.18);
  }
  .card--back {
    background: var(--brand-blue);
    display: flex;
    align-items: center;
    justify-content: center;
  }
  .brand {
    display: flex;
    align-items: center;
    gap: 14px;
    font-family: "Oswald", "Arial Narrow", sans-serif;
    font-weight: 500;
    text-transform: uppercase;
    line-height: 1;
  }
  .brand__square { width: 26px; height: 26px; flex: none; }
  .card--back .brand { color: var(--card-white); font-size: 46px; letter-spacing: 2px; }
  .card--back .brand__square { background: var(--card-white); width: 34px; height: 34px; }

  .card--front { background: var(--card-white); }
  .card__wave { position: absolute; inset: 0; width: 100%; height: 100%; }
  .card--front .brand {
    position: absolute;
    top: 64px;
    right: 36px;
    color: var(--brand-blue);
    font-size: 30px;
    letter-spacing: 1px;
  }
  .card--front .brand__square { background: var(--brand-blue); }
  .holder { position: absolute; top: 54px; left: 44px; }
  .holder__name {
    font-family: "Oswald", "Arial Narrow", sans-serif;
    font-weight: 500;
    font-size: 32px;
    color: var(--brand-blue);
    text-transform: uppercase;
    letter-spacing: -0.3px;
    line-height: 1;
  }
  .holder__title {
    font-size: 13px;
    letter-spacing: 1px;
    color: var(--ink);
    text-transform: uppercase;
    margin-top: 4px;
  }
  .contact { position: absolute; top: 146px; left: 64px; color: var(--ink); text-transform: uppercase; }
  .contact__row { display: flex; align-items: center; gap: 10px; }
  .contact__row--phone { font-size: 17px; }
  .contact__row--mail { font-size: 13px; margin-top: 4px; }
  .contact__icon { width: 20px; height: 20px; flex: none; }
  .contact__address { font-size: 13px; margin-top: 16px; line-height: 1.35; }
  .card__site {
    position: absolute;
    right: 40px;
    bottom: 34px;
    color: var(--card-white);
    font-size: 13px;
    letter-spacing: 0.5px;
    text-transform: uppercase;
  }
</style>
</head>
<body>
  <section class="card card--back">
    <div class="brand"><span class="brand__square"></span>Kestrel Facilities</div>
  </section>

  <section class="card card--front">
    <svg class="card__wave" viewBox="0 0 630 360" preserveAspectRatio="none" aria-hidden="true">
      <path d="M0,282 C180,280 330,246 450,180 C330,258 170,296 0,300 Z" fill="var(--swoosh-grey)"/>
      <path d="M0,308 C170,306 340,270 460,196 C525,156 575,138 630,126 L630,360 L0,360 Z" fill="var(--brand-blue)"/>
    </svg>

    <div class="brand"><span class="brand__square"></span>Kestrel Facilities</div>

    <div class="holder">
      <h1 class="holder__name">Daniel Reyes</h1>
      <p class="holder__title">Managing Director</p>
    </div>

    <div class="contact">
      <div class="contact__row contact__row--phone">
        <svg class="contact__icon" viewBox="0 0 24 24" aria-hidden="true">
          <path d="M6.6 10.8a15 15 0 0 0 6.6 6.6l2.2-2.2a1 1 0 0 1 1-.25 11.4 11.4 0 0 0 3.6.57 1 1 0 0 1 1 1V20a1 1 0 0 1-1 1A17 17 0 0 1 3 4a1 1 0 0 1 1-1h3.5a1 1 0 0 1 1 1c0 1.25.2 2.45.57 3.57a1 1 0 0 1-.25 1Z" fill="var(--brand-blue)"/>
        </svg>
        <span>044-555 010 227</span>
      </div>
      <div class="contact__row contact__row--mail">
        <svg class="contact__icon" viewBox="0 0 24 24" aria-hidden="true">
          <rect x="2" y="5" width="20" height="14" fill="var(--brand-blue)"/>
          <path d="M2 5l10 8 10-8" fill="none" stroke="#fff" stroke-width="1.6"/>
        </svg>
        <span>info@kestrelfm.com</span>
      </div>
      <p class="contact__address">18 Harbour Row,<br>Eastport, 30918</p>
    </div>

    <p class="card__site">www.kestrelfacilities.com</p>
  </section>
</body>
</html>
```